Website Design for Chef Wen Chinese Restaurant

Chef Wen is a new Chinese Restaurant. It offers exceptional dining experience with authentic and dynamic dishes created with quality ingredients.

A vivid website theme is required to promote this new restaurant online. Logo, menu, wine list and a few other files are attached for help with designing.

A very rough demo website has been setup and can be accessed via http://www.chefwen.com.au. It is for telling designers what content is shown up on each page (except for homepage). By reading the about us page, designers can get some more info of Chef Wen. However, the layout, theme color, font, etc are not set in stone. Visitors should be able to feel Chef Wen restaurant's authentic Chinese cuisine and high hygiene standard. Home page of the website could be The "Our website is coming soon" description is shown on demo site but do not required to be presented on new design.

Some main pages design should be included: Home (landing page), About us, Menu (Dishes), Winelist, Gallery, Contact us. No HTML and coding required. The output should be well layered psd or png files with acceptable resolution for web use.

A few other website can be referred to are:

http://larkspurasian.com.au/
http://www.river-lamp.com/
http://tamworthy.com.au/
http://harbelrestaurant.com.au/
http://www.quillerestaurant.com.au/
http://www.thekiln.com.au/

Industry/Entity Type

Restaurant

Requirements
Nice to have
• I expect designs of at least these webpages: homepage, menu page and contact us page. If you can provide "about us" page as well, it will probably help you win the competition. well layered psd or png file is my preference.
Should not have
• You don't have to make html/cs/js or any coding. All I need is just art design

```html
<!DOCTYPE html>
<html lang="en">
<head>
<meta charset="utf-8">
<title>Chef Wen Chinese Restaurant</title>
<link rel="stylesheet" href="https://fonts.googleapis.com/css2?family=Roboto:wght@400;700&family=Open+Sans:wght@400&family=Fira+Sans+Extra+Condensed:wght@400&family=Tinos:wght@400&display=swap">
<style>
:root{
  --cream:#fffdc8;
  --red:#f00000;
  --red-deep:#c80000;
  --red-dark:#ae0000;
  --white:#ffffff;
  --ink:#1a1a1a;
}
*{margin:0;padding:0;box-sizing:border-box}
html,body{width:994px;height:1200px;overflow:hidden}
body{position:relative;background:var(--cream);font-family:'Open Sans',sans-serif;color:var(--white)}
.abs{position:absolute}

.site-header{position:absolute;left:0;top:0;width:994px;height:132px;background:var(--cream)}
.brand-mark{position:absolute;left:482px;top:10px;width:30px;height:30px;background:var(--red)}
.brand-name{position:absolute;left:0;width:994px;top:60px;text-align:center;font-family:'Roboto',sans-serif;font-weight:700;font-size:19px;letter-spacing:1px;color:var(--red)}
.brand-sub{position:absolute;left:0;width:994px;top:104px;text-align:center;font-family:'Roboto',sans-serif;font-weight:700;font-size:10px;color:var(--ink);letter-spacing:.3px}

.main-nav{position:absolute;left:0;top:132px;width:994px;height:41px;background:linear-gradient(#ff1010,#d80000)}
.main-nav a{position:absolute;top:12px;transform:translateX(-50%);font-family:'Roboto',sans-serif;font-size:12px;color:var(--white);text-decoration:none;white-space:nowrap}

.hero{position:absolute;left:0;top:173px;width:994px;height:445px;background:radial-gradient(ellipse at 55% 45%,#c99a5e 0%,#a8743e 35%,#7a5a3a 65%,#555055 100%)}
.hero-title{position:absolute;left:0;width:994px;top:139px;text-align:center;font-family:'Fira Sans Extra Condensed',sans-serif;font-size:50px;letter-spacing:2px;color:var(--white)}
.hero-sub{position:absolute;left:0;width:994px;top:200px;text-align:center;font-family:'Tinos',serif;font-size:25px;letter-spacing:1px;color:var(--white)}
.hero-button{position:absolute;left:434px;top:250px;width:126px;height:44px;background:var(--red);border-radius:3px;text-align:center;line-height:44px;font-family:'Fira Sans Extra Condensed',sans-serif;font-size:14px;letter-spacing:.6px;color:var(--white)}
.slider-dots{position:absolute;left:470px;top:335px}
.slider-dots span{position:absolute;top:0;width:10px;height:10px;border:1px solid var(--white);border-radius:50%}
.slider-dots .active::after{content:"";position:absolute;left:2px;top:2px;width:4px;height:4px;border-radius:50%;background:var(--white)}

.feature-card{position:absolute;top:548px;width:262px;height:272px;background:linear-gradient(90deg,#e60000,#ff2020 50%,#e60000);border:5px solid var(--white);border-radius:3px;box-shadow:0 8px 10px rgba(0,0,0,.35)}
.feature-card h2{position:absolute;left:0;width:100%;top:30px;text-align:center;font-family:'Tinos',serif;font-weight:400;font-size:20px;color:var(--white)}
.feature-photo{position:absolute;left:14px;top:71px;width:224px;height:185px}

.site-footer{position:absolute;left:0;top:870px;width:994px;height:259px;background:linear-gradient(#ff0000,#cc0000)}
.footer-heading{position:absolute;top:30px;font-family:'Tinos',serif;font-weight:400;font-size:20px;color:var(--white);white-space:nowrap}
.divider{position:absolute;top:24px;width:1px;height:196px;background:rgba(255,255,255,.25)}
.hours-row{position:absolute;left:44px;font-size:12px;width:220px}
.hours-row span{position:absolute;left:101px;white-space:nowrap}
.cat{position:absolute;font-size:10.5px;white-space:nowrap}
.contact-line{position:absolute;font-size:10.5px;white-space:nowrap}
.social{position:absolute;left:808px;width:30px;height:30px;border:1.5px solid var(--white);border-radius:50%}
.social-label{position:absolute;left:851px;font-size:11px}

.copyright-bar{position:absolute;left:0;top:1129px;width:994px;height:71px;background:var(--red-dark)}
.copyright-bar p{position:absolute;left:0;width:994px;top:29px;text-align:center;font-size:9.5px}
</style>
</head>
<body>

<header class="site-header">
  <div class="brand-mark"></div>
  <div class="brand-name">CHEF WEN</div>
  <div class="brand-sub">CHEF WEN CHINESE RESTAURANT</div>
</header>

<nav class="main-nav">
  <a style="left:226px">Home</a>
  <a style="left:307px">About Us</a>
  <a style="left:388px">Menu</a>
  <a style="left:468px">Wine List</a>
  <a style="left:552px">Gallery</a>
  <a style="left:640px">Contact Us</a>
  <a style="left:746px">Larkspur Court</a>
</nav>

<section class="hero" role="img" aria-label="Photo of crispy spring rolls on a plate with lettuce and dipping sauce">
  <h1 class="hero-title">WELCOME TO CHEFWEN</h1>
  <p class="hero-sub">DELICIOUS FOOD</p>
  <div class="hero-button">VIEW OUR MENU</div>
  <div class="slider-dots">
    <span style="left:0"></span>
    <span class="active" style="left:21px"></span>
    <span style="left:42px"></span>
  </div>
</section>

<article class="feature-card" style="left:42px">
  <h2>ABOUT US</h2>
  <div class="feature-photo" role="img" aria-label="Photo of steamed dumplings in a bamboo basket" style="background:radial-gradient(circle at 50% 45%,#cfd3b8,#b9a27a 55%,#8e6a3e)"></div>
</article>
<article class="feature-card" style="left:364px">
  <h2>OUR FOOD</h2>
  <div class="feature-photo" role="img" aria-label="Photo of sliced raw salmon with garnish" style="background:linear-gradient(135deg,#f4e6e0,#ee5a44 35%,#e8402e 60%,#f2d8d0)"></div>
</article>
<article class="feature-card" style="left:690px">
  <h2>OUR DESSERT</h2>
  <div class="feature-photo" role="img" aria-label="Photo of a steamed red fish with shredded scallion" style="background:linear-gradient(135deg,#e8ddc8,#e25040 45%,#d83a2e 70%,#e6c9b0)"></div>
</article>

<footer class="site-footer">
  <h3 class="footer-heading" style="left:44px">TRADING HOURS</h3>
  <div class="hours-row" style="top:72px">Monday<span>11:30am -&nbsp; 2:30pm</span></div>
  <div class="hours-row" style="top:93px">Tuesday<span>11:30am -&nbsp; 2:30pm</span></div>
  <div class="hours-row" style="top:114px">Wednesday<span>11:30am -&nbsp; 2:30pm</span></div>
  <div class="hours-row" style="top:136px">Thursday<span>11:30am -&nbsp; 2:30pm</span></div>
  <div class="hours-row" style="top:157px">Friday<span>11:30am -&nbsp; 2:30pm</span></div>
  <div class="hours-row" style="top:178px">Saturday<span>11:00am -&nbsp; 3:30pm</span></div>
  <div class="hours-row" style="top:200px">Sunday<span style="left:103px">11:00am -&nbsp; 3:00pm</span></div>

  <div class="divider" style="left:271px"></div>

  <h3 class="footer-heading" style="left:300px">MAIN CATEGORY</h3>
  <div class="cat" style="left:302px;top:79px">Entrée</div>
  <div class="cat" style="left:302px;top:96px">Soup</div>
  <div class="cat" style="left:302px;top:113px">Cold Dishes</div>
  <div class="cat" style="left:302px;top:130px">Seafood Dishes</div>
  <div class="cat" style="left:302px;top:147px">Steak Dishes</div>
  <div class="cat" style="left:302px;top:164px">Chicken Dishes</div>
  <div class="cat" style="left:302px;top:181px">Duck Dishes</div>
  <div class="cat" style="left:302px;top:198px">Lamb Dishes</div>
  <div class="cat" style="left:415px;top:79px">Pork Dishes</div>
  <div class="cat" style="left:415px;top:96px">Tofu Dishes</div>
  <div class="cat" style="left:415px;top:113px">Hot Pot Dishes</div>
  <div class="cat" style="left:415px;top:130px">Vegetable Dishes</div>
  <div class="cat" style="left:415px;top:147px">Special flavour selections</div>
  <div class="cat" style="left:415px;top:164px">Abalone and Sea Cucumber</div>
  <div class="cat" style="left:415px;top:181px">Rice and Noodles</div>
  <div class="cat" style="left:415px;top:198px">Dessert</div>

  <div class="divider" style="left:572px"></div>

  <h3 class="footer-heading" style="left:603px">CONTACT US</h3>
  <div class="contact-line" style="left:605px;top:68px;font-size:13px">Chefwen</div>
  <svg class="abs" style="left:603px;top:101px" width="12" height="17" viewBox="0 0 12 17" aria-hidden="true"><path d="M6 0C2.7 0 0 2.6 0 5.9 0 10 6 17 6 17s6-7 6-11.1C12 2.6 9.3 0 6 0z" fill="#fff"/><circle cx="6" cy="6" r="2.2" fill="#e00000"/></svg>
  <div class="contact-line" style="left:627px;top:102px">12/48 Wattlebury Road</div>
  <div class="contact-line" style="left:627px;top:119px">Kent Town,</div>
  <div class="contact-line" style="left:627px;top:136px">SA, 5067</div>
  <svg class="abs" style="left:605px;top:172px" width="10" height="20" viewBox="0 0 10 20" aria-hidden="true"><path d="M7 0 9 4 6 6C5 8 5 12 6 14l3 2-2 4C3 19 1 15 1 10S3 1 7 0z" fill="#fff"/></svg>
  <div class="contact-line" style="left:627px;top:170px">Phone : 08 7010 4420</div>
  <div class="contact-line" style="left:666px;top:187px">08 7010 4431</div>

  <div class="divider" style="left:770px"></div>

  <h3 class="footer-heading" style="left:811px">GET CONNECT</h3>
  <div class="social" style="top:75px"></div>
  <div class="social-label" style="top:82px">Friendbook</div>
  <div class="social" style="top:123px"></div>
  <div class="social-label" style="top:132px">Chirper</div>
  <div class="social" style="top:171px"></div>
  <div class="social-label" style="top:180px">Circles +</div>
</footer>

<div class="copyright-bar">
  <p>Copyright © chefwen.com.2014</p>
</div>

</body>
</html>
```